we are an outdoor outlet in a country club that has a variety of outlets. The Club is called Meadowlark and is located in Cairo, Egypt. This garden menu will include cuisines from the Mediterranean, Asia and Texmex. we need a menu that is colorful and would fit an A3 size, back and front are to be used. Attached is the old menu currently in use (Garden Menu 2012.pdf is just for reference) and the new menu text for you to use is under the name Garden Menu Fall 2013
thank you.
Updates
Logo files have been uploaded for this project
Industry/Entity Type
Club
Look and feel
Each slider illustrates characteristics of the customer's brand and the style your logo design should communicate.

```html
<!DOCTYPE html>
<html lang="en">
<head>
<meta charset="utf-8">
<title>Garden Menu – Meadowlark</title>
<link href="https://fonts.googleapis.com/css2?family=Fredoka:wght@600&family=Pinyon+Script&family=Oswald:wght@400;500&family=Crimson+Text:ital@1&display=swap" rel="stylesheet">
<style>
:root{
  --page-bg:#e6e4d6;
  --paper:#f4f0e3;
  --lime:#a9cc1e;
  --lime-light:#c8e03a;
  --lime-dark:#86a814;
  --orange:#d8541f;
  --orange-dark:#c4461a;
  --brown:#5b3514;
  --ink:#3d2a14;
  --white:#ffffff;
  --club-green:#1f6b2a;
}
*{margin:0;padding:0;box-sizing:border-box}
html,body{width:1200px;height:1000px;overflow:hidden;background:var(--page-bg)}
.menu{position:absolute;left:270px;top:14px;width:660px;height:972px;background:var(--paper);box-shadow:0 2px 10px rgba(0,0,0,.18)}
.menu > *{position:absolute}
.frame{left:40px;top:34px;width:608px;height:902px;border:2px solid var(--lime)}
.header{left:48px;top:48px;width:588px;height:68px;background:linear-gradient(180deg,var(--lime-light),var(--lime));display:flex;align-items:center;justify-content:space-between;padding:0 14px 0 22px}
.header-title{font-family:'Fredoka',sans-serif;font-weight:600;font-size:52px;color:var(--white);letter-spacing:1px;line-height:1;white-space:nowrap}
.brand{display:flex;align-items:center;gap:6px;font-family:'Oswald',sans-serif;font-weight:500;font-size:24px;color:var(--club-green);white-space:nowrap}
.brand-dot{width:16px;height:16px;border-radius:50%;background:var(--club-green)}
.photo{border-radius:50%/40%}
.section-title{font-family:'Pinyon Script',cursive;color:var(--brown);font-size:36px;text-align:center;line-height:1;transform:translateX(-50%);white-space:nowrap}
.sub-title{font-family:'Pinyon Script',cursive;color:var(--brown);font-size:25px;text-align:center;line-height:1;transform:translateX(-50%);white-space:nowrap}
.ornament{width:18px;height:16px;background:var(--lime);border-radius:50% 50% 20% 20%;transform:translateX(-50%)}
.rule{height:1px;background:var(--lime)}
.item{transform:translateX(-50%);text-align:center;width:270px}
.item-name{font-family:'Oswald',sans-serif;font-weight:500;font-size:9.5px;color:var(--ink);letter-spacing:.2px;line-height:1.25;white-space:nowrap}
.item-desc{font-family:'Crimson Text',serif;font-style:italic;font-size:7.4px;color:var(--ink);line-height:1.25}
.box{background:var(--orange);border-radius:8px;padding:4px}
.box-inner{width:100%;height:100%;border:1px dashed rgba(255,255,255,.7);border-radius:6px;position:relative}
.box .sub-title,.box .item-name,.box .item-desc{color:var(--white)}
.box > .box-inner > *{position:absolute;left:50%}
.dessert{display:flex;align-items:flex-start;font-family:'Crimson Text',serif;font-style:italic;font-size:7.6px;color:var(--ink);line-height:1.2}
.dessert-bullet{width:6px;height:6px;background:var(--lime);border-radius:50%;margin:1px 6px 0 0;flex:none}
.dessert-name{width:100px}
.dessert-name.wide{width:158px}
.price{font-family:'Oswald',sans-serif;font-style:normal;font-size:7.6px;color:var(--ink);white-space:nowrap}
.badge{left:11px;top:881px;width:80px;height:80px;border-radius:50%;background:var(--lime);border:2px solid var(--white);box-shadow:0 0 0 2px var(--lime);display:flex;align-items:center;justify-content:center;text-align:center;font-family:'Oswald',sans-serif;font-weight:500;font-size:6.6px;color:var(--white);line-height:1.2;padding:10px}
</style>
</head>
<body>
<main class="menu">
  <div class="frame"></div>

  <header class="header">
    <h1 class="header-title">GARDEN MENU</h1>
    <div class="brand"><span class="brand-dot"></span>Meadowlark</div>
  </header>

  <!-- Asian Corner -->
  <div class="photo" role="img" aria-label="Plate of Mongolian beef with rice and chopsticks" style="left:443px;top:136px;width:188px;height:98px;background:radial-gradient(ellipse at 45% 50%,#4a2a18 0%,#7a4a2a 35%,#f2f0ec 62%,#e0ddd6 100%)"></div>
  <h2 class="section-title" style="left:338px;top:166px">Asian Corner</h2>
  <div class="ornament" role="img" aria-label="Leaf ornament" style="left:338px;top:208px"></div>

  <h3 class="sub-title" style="left:223px;top:244px">Salads &amp; Appetizers</h3>
  <div class="rule" style="left:130px;top:283px;width:186px"></div>
  <div class="ornament" role="img" aria-label="Leaf ornament" style="left:223px;top:276px;width:12px;height:10px"></div>

  <div class="item" style="left:223px;top:294px"><p class="item-name">CHICKEN WASABI SALAD | L.E. 00.00</p><p class="item-desc">Diced chicken with a mayo wasabi dressing on top of shredded lettuce</p></div>
  <div class="item" style="left:223px;top:324px;width:300px"><p class="item-name">CHICKEN SESAME NOODLE SALAD | L.E. 00.00</p><p class="item-desc">Sesame crusted chicken with glass noodles tossed with sweet chili, soy sauce, and lemongrass</p></div>
  <div class="item" style="left:223px;top:356px"><p class="item-name">SPRING ROLLS | L.E. 00.00</p><p class="item-desc">Vegetable spring rolls served with house made sweet and sour dip</p></div>
  <div class="item" style="left:223px;top:386px"><p class="item-name">INDIAN SAMOSA | L.E. 00.00</p><p class="item-desc">Fried dough parcels filled with vegetables and spices</p></div>

  <section class="box" style="left:359px;top:236px;width:240px;height:182px">
    <div class="box-inner">
      <h3 class="sub-title" style="top:10px">Main Courses</h3>
      <div class="item" style="top:42px;width:228px"><p class="item-name">MURGH CHICKEN MAKHNI | L.E. 00.00</p><p class="item-desc">Chicken cubes in a rich creamy tomato sauce seasoned with garam masala<br>Choice of side: vegetable korma or curd</p></div>
      <div class="item" style="top:84px;width:228px"><p class="item-name">CHICKEN TANDOORI | L.E. 00.00</p><p class="item-desc">Grilled chicken cubes with tandoori spices served with basmati rice</p></div>
      <div class="item" style="top:114px;width:228px"><p class="item-name">THAI COCONUT CURRY SHRIMP | L.E. 00.00</p><p class="item-desc">Sautéed shrimp tossed with curry and coconut milk served with jasmine rice</p></div>
      <div class="item" style="top:144px;width:228px"><p class="item-name">MONGOLIAN BEEF | L.E. 00.00</p><p class="item-desc">Soy marinated beef with oyster sauce and vegetables served with egg noodles</p></div>
    </div>
  </section>

  <!-- Tex Mex -->
  <div class="photo" role="img" aria-label="Plate of grilled chicken tacos" style="left:28px;top:406px;width:195px;height:100px;background:radial-gradient(ellipse at 50% 45%,#c9882f 0%,#b0542a 30%,#f4f1ea 60%,#ddd8cd 100%)"></div>
  <div class="rule" style="left:223px;top:486px;width:275px"></div>
  <h2 class="section-title" style="left:341px;top:438px">Tex Mex</h2>
  <div class="ornament" role="img" aria-label="Leaf ornament" style="left:341px;top:478px"></div>

  <h3 class="sub-title" style="left:200px;top:519px">Salads &amp; Appetizers</h3>
  <div class="rule" style="left:110px;top:555px;width:180px"></div>
  <div class="ornament" role="img" aria-label="Leaf ornament" style="left:200px;top:549px;width:12px;height:10px"></div>

  <div class="item" style="left:200px;top:566px"><p class="item-name">CAESAR SALAD | L.E. 00.00</p><p class="item-desc">Iceberg lettuce with Caesar dressing with grated<br>Parmesan cheese and croutons</p></div>
  <div class="item" style="left:200px;top:605px"><p class="item-name">TACO SALAD 42 | L.E. 00.00</p><p class="item-desc">Chicken breast, beans, sour cream, guacamole, tomato, corn,<br>lettuce, olives, chives, vinaigrette</p></div>
  <div class="item" style="left:200px;top:644px"><p class="item-name">NACHOS | L.E. 00.00</p><p class="item-desc">Topped with chili, melted cheese, beans</p></div>
  <div class="item" style="left:200px;top:675px"><p class="item-name">CHICKEN QUESADILLA | L.E. 00.00</p><p class="item-desc">served with guacamole, salsa, and sour cream</p></div>

  <section class="box" style="left:326px;top:512px;width:269px;height:184px">
    <div class="box-inner">
      <h3 class="sub-title" style="top:12px">Main Courses &amp; Sandwiches</h3>
      <div class="item" style="top:46px;width:258px"><p class="item-name">CHEESEBURGER | L.E. 00.00</p><p class="item-desc">House made lean beef burger topped with cheddar cheese</p></div>
      <div class="item" style="top:76px;width:258px"><p class="item-name">MUSHROOM BURGER | L.E. 00.00</p><p class="item-desc">Beef burger with sautéed mushroom, caramelized onion, and provolone cheese</p></div>
      <div class="item" style="top:106px;width:258px"><p class="item-name">CRISPY CHICKEN WRAP | L.E. 00.00</p><p class="item-desc">Crisp fried chicken wrap with a ranch dressing</p></div>
      <div class="item" style="top:136px;width:258px"><p class="item-name">FAJITA (CHICKEN, BEEF, COMBO) | L.E. 00.00</p><p class="item-desc">Pan seared meat or chicken with onion and bell pepper served with sour cream,<br>guacamole, salsa</p></div>
    </div>
  </section>

  <!-- Desserts -->
  <div class="photo" role="img" aria-label="Chocolate fondant with strawberries and blueberries" style="left:20px;top:691px;width:168px;height:100px;background:radial-gradient(ellipse at 50% 45%,#5a2e1a 0%,#7a3c22 25%,#f4f2ee 58%,#dcd9d2 100%)"></div>
  <h2 class="section-title" style="left:345px;top:716px">Desserts</h2>
  <div class="ornament" role="img" aria-label="Leaf ornament" style="left:345px;top:761px"></div>

  <div style="left:140px;top:794px;display:flex;flex-direction:column;gap:4.8px">
    <div class="dessert"><span class="dessert-bullet"></span><span class="dessert-name">Mix Berries Cheesecake</span><span class="price">| L.E. 00.00</span></div>
    <div class="dessert"><span class="dessert-bullet"></span><span class="dessert-name">Crème Brulee</span><span class="price">| L.E. 00.00</span></div>
    <div class="dessert"><span class="dessert-bullet"></span><span class="dessert-name">Chocolate Caramel Cake</span><span class="price">| L.E. 00.00</span></div>
    <div class="dessert"><span class="dessert-bullet"></span><span class="dessert-name">Warm Chocolate Fondant</span><span class="price">| L.E. 00.00</span></div>
    <div class="dessert"><span class="dessert-bullet"></span><span class="dessert-name">Baked Apple Tart Tatin</span><span class="price">| L.E. 00.00</span></div>
    <div class="dessert"><span class="dessert-bullet"></span><span class="dessert-name">Tiramisu</span><span class="price">| L.E. 00.00</span></div>
    <div class="dessert"><span class="dessert-bullet"></span><span class="dessert-name">Pumpkin Pie Flan</span><span class="price">| L.E. 00.00</span></div>
    <div class="dessert"><span class="dessert-bullet"></span><span class="dessert-name">Mixed Berries Granola Yoghurt</span><span class="price">| L.E. 00.00</span></div>
  </div>

  <div style="left:345px;top:794px;display:flex;flex-direction:column;gap:5px">
    <div class="dessert"><span class="dessert-bullet"></span><span class="dessert-name wide">Vanilla Ice Cream<br>Profiterole with dark and white chocolate sauce</span><span class="price">| L.E. 00.00</span></div>
    <div class="dessert"><span class="dessert-bullet"></span><span class="dessert-name wide">Caramelized Banana<br>with Deep Fried Ice Cream</span><span class="price">| L.E. 00.00</span></div>
    <div class="dessert"><span class="dessert-bullet"></span><span class="dessert-name wide">Baklava<br>with Nuts and Sugar Syrup</span><span class="price">| L.E. 00.00</span></div>
    <div class="dessert"><span class="dessert-bullet"></span><span class="dessert-name wide">Shot Glass Sampler<br>Tiramisu, Chocolate Crisp Mousse, Pear with Sabayon</span><span class="price">| L.E. 00.00</span></div>
    <div class="dessert"><span class="dessert-bullet"></span><span class="dessert-name wide">Ice Cream by Scoop</span><span class="price">| L.E. 00.00</span></div>
  </div>

  <p class="badge">PRICES ARE SUBJECT TO 12% SERVICE CHARGE AND 10% SALES TAX</p>
</main>
</body>
</html>
```